Tolbek cards

I want a simple business card that pops.
Logo on one side.
On side two i want.
"Are you thinking about a new building on your property, or renovating an existing structure? Contact".....
Owners Name: Dale Whitacre
Owners Phone number: 610-555-0187
Address:4076 Copper Ridge RD, Dunmere, PA 16099
Committed to Quality, Service, and Integrity

```html
<!DOCTYPE html>
<html lang="en">
<head>
<meta charset="utf-8">
<title>Tolbek Business Card</title>
<link rel="stylesheet" href="https://fonts.googleapis.com/css2?family=Montserrat:wght@400;500;800&display=swap">
<style>
  :root {
    --page-bg: #ecebe8;
    --card-white: #ffffff;
    --brown-dark: #4a2f1a;
    --brown-mid: #5c4129;
    --brown-light: #9b8670;
    --text-dark: #1e1e1e;
    --back-top: #9b8770;
    --back-bottom: #4d301a;
  }
  * { box-sizing: border-box; margin: 0; padding: 0; }
  html, body {
    width: 1181px;
    height: 1200px;
    overflow: hidden;
    background: var(--page-bg);
    font-family: "Montserrat", Arial, sans-serif;
  }
  .card {
    position: absolute;
    left: 220px;
    width: 746px;
    height: 425px;
    box-shadow: 0 4px 14px rgba(0,0,0,0.18);
    overflow: hidden;
  }
  .card-front { top: 126px; background: var(--card-white); }
  .card-back {
    top: 656px;
    background: linear-gradient(to bottom, var(--back-top), var(--back-bottom));
    display: flex;
    align-items: center;
    justify-content: center;
  }
  .owner-name {
    position: absolute;
    left: 26px;
    top: 80px;
    font-size: 31px;
    font-weight: 800;
    color: var(--brown-dark);
    letter-spacing: 0.5px;
  }
  .tagline {
    position: absolute;
    left: 26px;
    top: 123px;
    font-size: 16.5px;
    font-weight: 500;
    color: var(--brown-dark);
  }
  .divider {
    position: absolute;
    top: 162px;
    height: 3px;
  }
  .divider-dark { left: 26px; width: 94px; background: var(--brown-dark); }
  .divider-light { left: 124px; width: 45px; background: var(--brown-light); }
  .contact-row {
    position: absolute;
    left: 26px;
    display: flex;
    align-items: center;
    gap: 12px;
    font-size: 22px;
    color: var(--text-dark);
  }
  .contact-row svg { width: 28px; height: 28px; flex: none; }
  .phone-row { top: 193px; }
  .address-row { top: 238px; }
  .pitch {
    position: absolute;
    left: 26px;
    top: 293px;
    width: 560px;
    font-size: 21.5px;
    line-height: 28px;
    color: var(--text-dark);
  }
  .stripes {
    position: absolute;
    left: 0;
    top: 0;
    width: 746px;
    height: 425px;
  }
  .brand-name {
    position: absolute;
    right: 26px;
    top: 76px;
    display: flex;
    align-items: center;
    gap: 10px;
    font-size: 44px;
    font-weight: 800;
    color: var(--brown-mid);
    letter-spacing: 1px;
  }
  .brand-square {
    width: 22px;
    height: 22px;
    background: var(--brown-light);
  }
  .back-brand {
    font-size: 72px;
    font-weight: 800;
    color: var(--card-white);
    letter-spacing: 2px;
  }
</style>
</head>
<body>
  <section class="card card-front">
    <svg class="stripes" viewBox="0 0 746 425" aria-hidden="true">
      <polygon points="652,290 689,290 560,425 504,425" fill="var(--brown-light)"/>
      <polygon points="705,290 746,290 746,297 619,425 560,425" fill="var(--brown-mid)"/>
    </svg>

    <h1 class="owner-name">DALE WHITACRE</h1>
    <p class="tagline">Committed to Quality, Service, and Integrity</p>
    <span class="divider divider-dark"></span>
    <span class="divider divider-light"></span>

    <p class="contact-row phone-row">
      <svg viewBox="0 0 28 28" aria-hidden="true">
        <circle cx="14" cy="14" r="13" fill="var(--brown-dark)"/>
        <path d="M9.5 7.5c.6-.4 1.4-.3 1.8.3l1.4 2.2c.3.5.2 1.1-.2 1.5l-.9.8c.7 1.6 1.9 2.9 3.5 3.7l.8-.9c.4-.4 1-.5 1.5-.2l2.2 1.3c.6.4.8 1.2.4 1.8l-.8 1.1c-.5.7-1.4 1-2.3.8-4.3-1-7.7-4.4-8.7-8.7-.2-.9.1-1.8.8-2.3z" fill="#fff"/>
      </svg>
      610-555-0187
    </p>
    <p class="contact-row address-row">
      <svg viewBox="0 0 28 28" aria-hidden="true">
        <circle cx="14" cy="14" r="13" fill="var(--brown-dark)"/>
        <path d="M14 6.5a5 5 0 0 0-5 5c0 3.7 5 9.5 5 9.5s5-5.8 5-9.5a5 5 0 0 0-5-5z" fill="#fff"/>
        <circle cx="14" cy="11.5" r="1.9" fill="var(--brown-dark)"/>
      </svg>
      4076 Copper Ridge RD, Dunmere, PA 16099
    </p>

    <p class="pitch">Are you thinking about a new building on your property, or renovating an existing structure? Contact</p>

    <div class="brand-name">
      <span class="brand-square"></span>
      <span>TOLBEK</span>
    </div>
  </section>

  <section class="card card-back">
    <span class="back-brand">TOLBEK</span>
  </section>
</body>
</html>
```